Wordpress Design Project for Employee Communications Site

We need a Wordpress design for a company that strategizes on and produces materials for employee communications. Improving employee communications at all levels of an organization can help improve overall company performance and results. The site needs to look very clean and professional; we're not afraid of white space. We like the functionality that Wordpress provides; however, we only want one "true" blog page; the other pages should give the impression of a more "static" web site - particularly the home page. I have a logo that I can provide.

I have added these comments to the discussion page:
Great question - thank you for asking it. I’ve done more research

I like the very clean and monochromatic looks to many of these. I don’t have to have monochromatic, but I do like minimal colors. Simple, clean, organized. The home page should “fit” almost entirely without scrolling. I do like fat footers that you can scroll down to. I don’t want a colored background, but any that I’ve chosen with colored backgrounds could be switched to a white background.

http://www.mirabelquennet.example/
http://pondraft.example/
http://v1.samplumworth.example/
http://howdythegoat.example/
http://stayingbrisk.example/
http://www.interiors.kelmun.example/
http://trelvmasters.example/

These last two are more corporate sites. The first one is from a well-respected consultant in my area who does a lot of what I do. And I think Harwenby does a nice job with their site. So, I want to marry the look I like with getting the content job done.

http://www.messagefuelbox.example/
http://www.harwenby.example/view/en_US/us/index.htm

Target Market(s)

Target market is mid- to large-sized companies. More than 500 employees.

Industry/Entity Type

Communications

Requirements
Must have
• Need an impactful home page. There should be a "blog" page; contact us; services; about. For starters, at least. I want fonts to be very readable - that is, either quite dark gray or black.
Nice to have
• I am loathe to include a picture of myself, but I do want some images that say, "professional" and "expert" in communications.
Should not have
• I don't want a hits counter :) (I know no one would do that!).

```html
<!DOCTYPE html>
<html lang="en">
<head>
<meta charset="utf-8">
<title>Teamvoice Communications</title>
<link href="https://fonts.googleapis.com/css2?family=Ubuntu:ital,wght@0,400;0,500;1,400&display=swap" rel="stylesheet">
<style>
:root{
  --green:#9dc41a;
  --green-dark:#86a912;
  --cyan:#1fb4e6;
  --cyan-dark:#0f9fd2;
  --heading-blue:#1a9fd6;
  --text:#555;
  --dark:#333;
  --band:#ebebeb;
  --footer:#f0f0f0;
  --white:#fff;
  --bullet:#c4161c;
}
*{box-sizing:border-box;margin:0;padding:0}
html,body{width:1200px;height:1180px;overflow:hidden}
body{position:relative;background:var(--white);font-family:"Ubuntu",sans-serif;color:var(--text)}
a{color:inherit;text-decoration:none}

.site-header{position:absolute;left:0;top:0;width:1200px;height:130px;background:var(--white)}
.brand{position:absolute;left:143px;top:46px;width:370px;display:flex;align-items:center;gap:12px;white-space:nowrap}
.brand-dot{flex:none;width:30px;height:30px;border-radius:50%;background:var(--cyan)}
.brand-name{font-size:24px;font-weight:400;color:var(--green);letter-spacing:.3px}

.main-nav{position:absolute;left:530px;top:50px;width:540px;height:43px;display:flex;border-radius:4px;overflow:hidden;background:var(--cyan)}
.main-nav a{display:flex;align-items:center;justify-content:center;color:var(--white);font-size:14px;font-weight:500;border-right:1px solid var(--cyan-dark);background:linear-gradient(#29bdee,#12a8dc)}
.main-nav a:last-child{border-right:0}
.main-nav a.is-active{background:linear-gradient(#acd126,#91b913)}
.nav-shadow{position:absolute;left:550px;top:100px;width:510px;height:8px;background:radial-gradient(ellipse at center,rgba(0,0,0,.14),rgba(0,0,0,0) 70%)}

.hero-band{position:absolute;left:0;top:130px;width:1200px;height:402px;background:var(--band)}
.slider{position:absolute;left:130px;top:152px;width:940px;height:418px;background:var(--white);padding:6px;box-shadow:0 1px 4px rgba(0,0,0,.18)}
.slide-image{width:928px;height:406px;background:linear-gradient(100deg,#d9dee2 0%,#c8d4de 30%,#b6c9dc 55%,#e4e7ea 80%,#cfd5da 100%)}
.slider-dots{position:absolute;left:31px;top:378px;display:flex;gap:8px}
.slider-dots span{width:20px;height:20px;border-radius:50%;background:radial-gradient(circle at 40% 35%,#9be3ff,var(--cyan));box-shadow:0 1px 2px rgba(0,0,0,.3)}
.slider-dots span.is-current{background:radial-gradient(circle at 40% 35%,#d6ef6a,var(--green-dark))}

.panel{position:absolute;top:570px;width:300px;height:310px;padding:23px 21px 22px 19px;background:linear-gradient(#f2f2f2,#fafafa 70%,#fff)}
.panel h2{font-size:24px;font-weight:400;color:var(--dark);margin-bottom:12px}
.panel h2 em{font-style:normal;color:var(--heading-blue)}
.panel p{font-size:12.5px;line-height:20px}
.panel p+p{margin-top:15px}
.panel-welcome{left:130px}
.panel-services{left:450px}
.panel-blog{left:770px;padding-right:19px}
.service-list{list-style:none;font-size:12.5px}
.service-list li{position:relative;padding-left:20px;height:30.3px;line-height:20px}
.service-list li::before{content:"";position:absolute;left:1px;top:6px;width:0;height:0;border-left:6px solid var(--bullet);border-top:4px solid transparent;border-bottom:4px solid transparent}
.post-meta{display:flex;justify-content:space-between;font-size:11px;font-style:italic;color:#888;margin-top:12px}
.post-meta .author{color:var(--heading-blue)}
.post+.post{border-top:1px solid #ddd;margin-top:16px;padding-top:18px}
.post p{font-size:12.5px;line-height:20px}

.more-btn{position:absolute;top:862px;width:59px;height:40px;display:flex;align-items:center;justify-content:center;font-size:14px;font-weight:500;color:var(--dark);background:linear-gradient(#acd126,#91b913);border-bottom:2px solid #6f8f0b}

.site-footer{position:absolute;left:0;top:925px;width:1200px;height:255px;background:var(--footer);border-top:1px solid #ddd}
.footer-col{position:absolute;top:26px}
.footer-col h3{font-size:17px;font-weight:400;color:var(--dark);margin-bottom:14px}
.news{left:130px;width:294px}
.news time{display:block;font-size:13px;font-style:italic;font-weight:500;color:var(--heading-blue);margin-bottom:3px}
.news p{font-size:12.5px;line-height:20px;color:#444}
.news .read-more{display:inline-block;font-size:12.5px;font-weight:500;color:var(--dark);text-decoration:underline;margin-top:1px}
.quick{left:490px}
.link-list{list-style:none;font-size:11.5px;color:#444;margin-top:-4px}
.link-list li{height:25.6px;line-height:16px;display:flex;align-items:center;gap:14px}
.arrow{width:7px;height:7px}
.connect{left:691px}
.social-icon{width:16px;height:16px;border-radius:2px;background:#7a8ea6}
.social-icon.rss{background:#e88a2a}
.connect .link-list li{gap:10px;height:26px}
.newsletter{left:849px;width:221px}
.email-input{width:220px;height:26px;border:1px solid #ccc;background:var(--white);font-size:11.5px;font-style:italic;color:#999;padding:0 9px;line-height:24px}
.go-btn{margin:10px 0 0 auto;width:36px;height:25px;border-radius:2px;background:var(--cyan);color:var(--dark);font-size:12px;font-weight:500;display:flex;align-items:center;justify-content:center}
.footer-brand{display:flex;align-items:center;gap:6px;margin-top:36px;white-space:nowrap}
.footer-brand .dot{width:16px;height:16px;border-radius:50%;background:#999}
.footer-brand span{font-size:14px;color:#999}
.copyright{font-size:11px;color:#777;margin-top:22px;letter-spacing:.2px}
</style>
</head>
<body>
<header class="site-header">
  <div class="brand"><div class="brand-dot"></div><span class="brand-name">Teamvoice Communications</span></div>
  <nav class="main-nav">
    <a href="#" class="is-active" style="width:98px">Home</a>
    <a href="#" style="width:117px">About Us</a>
    <a href="#" style="width:110px">Services</a>
    <a href="#" style="width:84px">Blog</a>
    <a href="#" style="width:131px">Contact Us</a>
  </nav>
  <div class="nav-shadow"></div>
</header>

<div class="hero-band"></div>
<section class="slider">
  <div class="slide-image" role="img" aria-label="Photo of a customer service professional with a headset working in a bright office"></div>
  <div class="slider-dots"><span class="is-current"></span><span></span><span></span><span></span><span></span></div>
</section>

<section class="panel panel-welcome">
  <h2><em>Welcome</em> to Our Site</h2>
  <p>Lorem ipsum dolor sit amet, consectetur adipiscing elit. Fusce accumsan, elit a suscipit sagittis, tortor sapien cursus risus, non rhon-cus lectus nunc ac nulla.</p>
  <p>Aliquam molestie, mi et imperdiet euismod, dui purus auctor tellus, et interdum lacus lectus et ante. Sed accumsan sollicitudin sapien, sit amet adipiscing turpis gravida ac.<br>In congue.</p>
</section>
<section class="panel panel-services">
  <h2><em>Our</em> Services</h2>
  <ul class="service-list">
    <li>Fusce accumsan, elit a suscipit sagittis.</li>
    <li>Tortor sapien cursus risus.</li>
    <li>Non rhoncus lectus nunc ac nulla.</li>
    <li>Aliquam molestie.</li>
    <li>Mi et imperdiet euismod.</li>
    <li>Dui purus auctor tellus, et interdum lacus.</li>
    <li>Sed accumsan sollicitudin sapien.</li>
  </ul>
</section>
<section class="panel panel-blog">
  <h2><em>Recent</em> Blog</h2>
  <article class="post">
    <p>Vestibulum ante ipsum primis in faucibus orci luctus et ultrices posuere cubilia Curae; Ut et scelerisque ante.</p>
    <div class="post-meta"><span>Posted on Aug02, 2012</span><span class="author">By Colin Varde</span></div>
  </article>
  <article class="post">
    <p>Vestibulum ante ipsum primis in faucibus orci luctus et ultrices posuere cubilia Curae; Ut et scelerisque ante.</p>
    <div class="post-meta"><span>Posted on Aug02, 2012</span><span class="author">By Colin Varde</span></div>
  </article>
</section>
<a href="#" class="more-btn" style="left:251px">More</a>
<a href="#" class="more-btn" style="left:571px">More</a>
<a href="#" class="more-btn" style="left:891px">More</a>

<footer class="site-footer">
  <div class="footer-col news">
    <h3>Latest News</h3>
    <time>Aug 04,2012</time>
    <p>Lorem ipsum dolor sit amet, consectetur adipiscing elit. Fusce accumsan, elit a suscipit sagittis, tortor sapien cursus risus, non rhoncus lectus nunc ac<br>nulla.</p>
    <a href="#" class="read-more">Read More</a>
  </div>
  <div class="footer-col quick">
    <h3>Quick Links</h3>
    <ul class="link-list">
      <li><svg class="arrow" viewBox="0 0 7 7"><path d="M0 3.5h6M4 1.5l2 2-2 2" stroke="#333" fill="none"/></svg>Home</li>
      <li><svg class="arrow" viewBox="0 0 7 7"><path d="M0 3.5h6M4 1.5l2 2-2 2" stroke="#333" fill="none"/></svg>About us</li>
      <li><svg class="arrow" viewBox="0 0 7 7"><path d="M0 3.5h6M4 1.5l2 2-2 2" stroke="#333" fill="none"/></svg>Services</li>
      <li><svg class="arrow" viewBox="0 0 7 7"><path d="M0 3.5h6M4 1.5l2 2-2 2" stroke="#333" fill="none"/></svg>Blog</li>
      <li><svg class="arrow" viewBox="0 0 7 7"><path d="M0 3.5h6M4 1.5l2 2-2 2" stroke="#333" fill="none"/></svg>Contact Us</li>
    </ul>
  </div>
  <div class="footer-col connect">
    <h3>Connect Us</h3>
    <ul class="link-list">
      <li><span class="social-icon"></span>Friendwall</li>
      <li><span class="social-icon"></span>Chirper</li>
      <li><span class="social-icon"></span>Circlespace</li>
      <li><span class="social-icon rss"></span>Rss Feed</li>
    </ul>
  </div>
  <div class="footer-col newsletter">
    <h3>Newsletter SignUp</h3>
    <div class="email-input">enter email address</div>
    <div class="go-btn">GO</div>
    <div class="footer-brand"><span class="dot"></span><span>Teamvoice Communications</span></div>
    <p class="copyright">Copyright © 2012, All Rights Reserved.</p>
  </div>
</footer>
</body>
</html>
```